High Tech Real Estate Startup needs a business card

We are developing an innovative real estate marketing product based around advanced search and virtual reality.

We talk to people, we need business cards.

Target Market(s)

The target market is technology professionals and realtors.

Contact Information for Business Card

The information to be included will include

Name
Title
Phone Number
E-mail Address
www.zelquin.com

It should use simple iconography for each one of those fields.

Font styles to use
Other font styles liked:
• Co, Jubilat, Avenir

Colors

Designer to choose colors to be used in the design.

Requirements
Must have
• Clean aesthetic,
• Good use of negative space.
• It should use our company logo, shown in the attached file. It is able to use the negative of that logo (coloured font and white background) and I have attached other acceptable accent colours in a swatch file.
Should not have
• Should not be too busy
• No extraneous text (slogans, tag lines etc)

```html
<!DOCTYPE html>
<html lang="en">
<head>
<meta charset="utf-8">
<title>Zelquin Business Card</title>
<link href="https://fonts.googleapis.com/css2?family=Open+Sans:wght@400;500;600;700&display=swap" rel="stylesheet">
<style>
  :root {
    --backdrop: #3b3b3d;
    --teal: #3aa9ae;
    --teal-deep: #2a8c91;
    --paper: #f1f1f1;
    --charcoal: #3f4145;
    --white: #ffffff;
  }
  html, body {
    margin: 0;
    padding: 0;
    width: 799px;
    height: 1200px;
    overflow: hidden;
    background: var(--backdrop);
    font-family: "Open Sans", Arial, sans-serif;
  }
  .canvas {
    position: relative;
    width: 799px;
    height: 1200px;
  }
  .card {
    position: absolute;
    left: 90px;
    width: 620px;
    height: 354px;
    border-radius: 26px;
    overflow: hidden;
  }
  .card-front {
    top: 123px;
    background: var(--teal);
    display: flex;
    align-items: center;
    justify-content: center;
  }
  .front-name {
    font-size: 64px;
    font-weight: 500;
    letter-spacing: 4px;
    color: var(--teal-deep);
  }
  .card-back {
    top: 723px;
    background: var(--teal);
  }
  .back-shapes {
    position: absolute;
    inset: 0;
  }
  .back-name {
    position: absolute;
    left: 40px;
    top: 128px;
    font-size: 46px;
    font-weight: 500;
    letter-spacing: 3px;
    color: var(--teal);
  }
  .contact {
    position: absolute;
    left: 370px;
    top: 148px;
    color: var(--white);
  }
  .person-name {
    font-size: 27px;
    font-weight: 600;
    margin: 0;
    line-height: 1.1;
  }
  .person-title {
    font-size: 15px;
    font-weight: 400;
    margin: 2px 0 14px;
  }
  .contact-list {
    list-style: none;
    margin: 0;
    padding: 0;
    font-size: 16px;
  }
  .contact-list li {
    display: flex;
    align-items: center;
    gap: 10px;
    height: 22px;
  }
  .contact-icon {
    width: 16px;
    height: 16px;
    flex: none;
  }
  .icon-spacer {
    width: 16px;
    flex: none;
  }
</style>
</head>
<body>
<div class="canvas">
  <section class="card card-front">
    <span class="front-name">ZELQUIN</span>
  </section>

  <section class="card card-back">
    <svg class="back-shapes" viewBox="0 0 620 354" width="620" height="354">
      <path d="M0 0 H322 C362 110 350 250 262 354 H0 Z" fill="var(--charcoal)"/>
      <path d="M0 0 H310 C346 110 330 250 236 354 H0 Z" fill="var(--paper)"/>
    </svg>
    <span class="back-name">ZELQUIN</span>
    <div class="contact">
      <h1 class="person-name">Jane Roe Miller</h1>
      <p class="person-title">Managing Director</p>
      <ul class="contact-list">
        <li>
          <svg class="contact-icon" viewBox="0 0 16 16"><circle cx="8" cy="8" r="7.5" fill="none" stroke="#fff"/><path d="M5.2 4.5h1.6l.7 1.8-1 .7a5 5 0 0 0 2.5 2.5l.7-1 1.8.7v1.6c-3.5.3-6.6-2.8-6.3-6.3z" fill="#fff"/></svg>
          <span>555.555.5555</span>
        </li>
        <li>
          <svg class="contact-icon" viewBox="0 0 16 16"><circle cx="8" cy="8" r="7.5" fill="none" stroke="#fff"/><rect x="4" y="5.2" width="8" height="5.6" fill="#fff"/><path d="M4 5.4 8 8.4 12 5.4" fill="none" stroke="var(--teal)" stroke-width="0.9"/></svg>
          <span>janeroe@zelquin.com</span>
        </li>
        <li>
          <svg class="contact-icon" viewBox="0 0 16 16"><circle cx="8" cy="8" r="7.5" fill="none" stroke="#fff"/><circle cx="8" cy="8" r="4" fill="none" stroke="#fff" stroke-width="1.1"/><path d="M4 8h8M8 4c-2 2.4-2 5.6 0 8M8 4c2 2.4 2 5.6 0 8" fill="none" stroke="#fff" stroke-width="0.9"/></svg>
          <span>www.zelquin.com</span>
        </li>
      </ul>
    </div>
  </section>
</div>
</body>
</html>
```